Dynamic Business Card for Sports Supplements Company

Hi! I'm looking for an awesome business card to match my existing sports supplement company. I have uploaded my current company logo and screenshot of the front page of my website.

I would like to have something dynamic and interesting and utilize the colors in the website - the reds and purples

The business card should be double sided and focus on a unique eye-catching design on the back and include all the relevant company info.

Most importantly, it should say somewhere: "Sign up on our website for a coupon code."

Target Market(s)

Mostly for women gym goers but it shouldn't be too feminine. It should be in keeping with the website design. It should flow and clearly be connected to it

Industry/Entity Type

Business

Contact Information for Business Card

Lorraine K. Vestal
CEO
LVestal@Quorvanexco.com
www.quorvanexco.com
555.417.3820
P.O. Box 47315
Larkmere, Ohio 00000

Sign up on our website for a coupon code

Font styles to use
Serif
Sans Serif
Other font styles liked:
• Novecento font family and "Quorvanex" is in AR Destine font

Requirements
Must have
• One side should be a bold Quorvanex logo design. Even just the symbol itself may be o.k. (see attached file)

```html
<!DOCTYPE html>
<html lang="en">
<head>
<meta charset="utf-8">
<title>Quorvanex Business Card</title>
<link rel="stylesheet" href="https://fonts.googleapis.com/css2?family=Exo+2:wght@700;800&family=Open+Sans:wght@400;600&display=swap">
<style>
  :root {
    --navy: #2b3447;
    --navy-light: #3a4459;
    --navy-dark: #1f2636;
    --charcoal: #222326;
    --charcoal-light: #2c2d31;
    --red: #d4232f;
    --white: #ffffff;
    --grey-line: #8a8c92;
    --canvas-bg: #e9e7e3;
  }
  * { margin: 0; padding: 0; box-sizing: border-box; }
  html, body {
    width: 1200px; height: 780px; overflow: hidden;
    background: var(--canvas-bg);
    font-family: "Open Sans", Arial, sans-serif;
  }
  .canvas { position: relative; width: 1200px; height: 780px; }

  .card {
    position: absolute;
    overflow: hidden;
    border-radius: 4px;
    box-shadow: 0 10px 28px rgba(0,0,0,.22);
  }

  /* ---------- Front (portrait) ---------- */
  .card-front { left: 90px; top: 90px; width: 360px; height: 600px; }
  .card-front .shapes { position: absolute; inset: 0; }
  .front-brand {
    position: absolute; top: 70px; left: 0; right: 0;
    display: flex; align-items: center; justify-content: center; gap: 12px;
  }
  .brand-mark { width: 26px; height: 26px; background: var(--red); }
  .brand-name {
    font-family: "Exo 2", Arial, sans-serif; font-weight: 800;
    color: var(--white); text-transform: uppercase; letter-spacing: 1px;
  }
  .front-brand .brand-name { font-size: 38px; }
  .person { position: absolute; top: 150px; left: 0; right: 0; text-align: center; }
  .person-name {
    font-family: "Exo 2", Arial, sans-serif; font-weight: 800;
    font-size: 25px; color: var(--red); letter-spacing: .5px;
  }
  .person-title { font-size: 15px; color: var(--white); }

  .contact { position: absolute; top: 318px; left: 30px; right: 30px; text-align: center; color: var(--white); }
  .contact-label { font-size: 14px; font-weight: 600; color: var(--red); }
  .contact-value { font-size: 17px; line-height: 1.3; }
  .contact-divider {
    height: 1px; margin: 10px 0;
    background: linear-gradient(90deg, transparent, var(--grey-line) 20%, var(--grey-line) 80%, transparent);
  }
  .website {
    position: absolute; left: 0; right: 0; bottom: 28px;
    text-align: center; color: var(--white); font-size: 17px; letter-spacing: .5px;
  }

  /* ---------- Back (landscape) ---------- */
  .card-back { left: 520px; top: 215px; width: 600px; height: 350px; }
  .card-back .surface {
    position: absolute; inset: 0;
    background: radial-gradient(ellipse at 55% 45%, var(--navy-light), var(--navy) 55%, var(--navy-dark));
  }
  .coupon-band {
    position: absolute; left: 0; top: 0; bottom: 0; width: 66px;
    background: var(--red);
    border-right: 4px solid var(--white);
  }
  .coupon-text {
    position: absolute; left: 31px; top: 50%;
    transform: translate(-50%, -50%) rotate(90deg);
    white-space: nowrap; color: var(--white); font-size: 16px; letter-spacing: .2px;
  }
  .back-brand {
    position: absolute; left: 66px; right: 0; top: 0; bottom: 0;
    display: flex; align-items: center; justify-content: center; gap: 18px;
  }
  .back-brand .brand-mark { width: 40px; height: 40px; }
  .back-brand .brand-name { font-size: 62px; }
</style>
</head>
<body>
<main class="canvas">

  <section class="card card-front" aria-label="Business card front">
    <svg class="shapes" width="360" height="600" viewBox="0 0 360 600" aria-hidden="true">
      <defs>
        <radialGradient id="chalkNavy" cx="50%" cy="30%" r="75%">
          <stop offset="0" stop-color="#3a4459"/>
          <stop offset="1" stop-color="#242c3d"/>
        </radialGradient>
        <linearGradient id="charcoalFill" x1="0" y1="0" x2="0" y2="1">
          <stop offset="0" stop-color="#2c2d31"/>
          <stop offset="1" stop-color="#1c1d20"/>
        </linearGradient>
      </defs>
      <rect class="navy-panel" width="360" height="600" fill="url(#chalkNavy)"/>
      <path class="white-chevron" d="M0 212 L180 268 L360 212 V600 H0 Z" fill="#ffffff"/>
      <path class="charcoal-panel" d="M0 236 L180 292 L360 236 V600 H0 Z" fill="url(#charcoalFill)"/>
      <rect class="red-edge-line" x="0" y="514" width="360" height="4" fill="#ffffff"/>
      <rect class="red-band" x="0" y="518" width="360" height="82" fill="#d4232f"/>
    </svg>

    <div class="front-brand">
      <span class="brand-mark"></span>
      <span class="brand-name">Quorvanex</span>
    </div>

    <div class="person">
      <div class="person-name">Lorraine K. Vestal</div>
      <div class="person-title">CEO</div>
    </div>

    <div class="contact">
      <div class="contact-label">Phone</div>
      <div class="contact-value">555.417.3820</div>
      <div class="contact-divider"></div>
      <div class="contact-label">Email</div>
      <div class="contact-value">LVestal@Quorvanexco.com</div>
      <div class="contact-divider"></div>
      <div class="contact-value">P.O. Box 47315</div>
      <div class="contact-value">Larkmere, Ohio 00000</div>
    </div>

    <div class="website">www.quorvanexco.com</div>
  </section>

  <section class="card card-back" aria-label="Business card back">
    <div class="surface"></div>
    <div class="coupon-band">
      <span class="coupon-text">Sign up on our website for a coupon code</span>
    </div>
    <div class="back-brand">
      <span class="brand-mark"></span>
      <span class="brand-name">Quorvanex</span>
    </div>
  </section>

</main>
</body>
</html>
```